Business Card Update, need to bring life to the card, two sided color

We need a new business card design, are moving and changing addresses and need a new look, we have the logos already attached but need a new style moving forward. Can incorporate the color of the logo (The Green) as well, maybe a solid back? We deal with safety products revolving around static electricity and safety lighting. Would like to keep same font in second logo as well.

Target Market(s)

Electrical Safety, Lighting

Contact Information for Business Card

Dale Fenwick
Vice President
Office: 770-555-4821
Cell: 770-555-3067
dale@tkfenwick.example
www.tkfenwick.example
4700 West Harbor Boulevard
Suite #150
Roswell, GA 30076

Font styles to use
Serif
Sans Serif

Requirements
Must have
• Since 1918
Nice to have
• Could use the 100 Year Logo for back of card, would like the back of card to be the same green as logo.
Should not have
• No black cards please.

```html
<!DOCTYPE html>
<html lang="en">
<head>
<meta charset="utf-8">
<title>T.K. Fenwick Business Card</title>
<link href="https://fonts.googleapis.com/css2?family=Arimo:wght@700&family=Lato:wght@700&family=Open+Sans:wght@400;600&display=swap" rel="stylesheet">
<style>
  :root {
    --backdrop: #3c3c3c;
    --brand-green: #00985a;
    --card-white: #f3f3f3;
    --ink: #2a2a2a;
    --white: #ffffff;
  }
  * { margin: 0; padding: 0; box-sizing: border-box; }
  html, body { width: 1200px; height: 900px; overflow: hidden; }
  body {
    background: var(--backdrop);
    position: relative;
    font-family: "Open Sans", Arial, sans-serif;
  }
  .card {
    position: absolute;
    top: 200px;
    width: 310px;
    height: 502px;
    box-shadow: 2px 3px 4px rgba(0,0,0,0.45);
  }
  .card-front {
    left: 253px;
    background: var(--card-white);
    border-radius: 62px 0 62px 0;
  }
  .card-back {
    left: 627px;
    background: var(--brand-green);
    border-radius: 0 62px 0 62px;
  }
  .brand-mark {
    position: absolute;
    left: 0; right: 0;
    display: flex;
    align-items: center;
    justify-content: center;
    gap: 8px;
    font-family: "Arimo", Arial, sans-serif;
    font-weight: 700;
  }
  .brand-mark .dot {
    border-radius: 50%;
    flex: none;
  }
  .card-front .brand-mark {
    top: 96px;
    color: var(--brand-green);
    font-size: 17px;
  }
  .card-front .brand-mark .dot {
    width: 16px; height: 16px;
    background: var(--brand-green);
  }
  .company {
    position: absolute;
    top: 184px;
    left: 0; right: 0;
    text-align: center;
    color: var(--brand-green);
    font-family: "Arimo", Arial, sans-serif;
    font-weight: 700;
  }
  .company-name { font-size: 25px; line-height: 28px; }
  .company-sub { font-size: 12.5px; line-height: 14px; }
  .contact {
    position: absolute;
    left: 31px;
    top: 290px;
    color: var(--ink);
  }
  .person-name {
    font-family: "Lato", Arial, sans-serif;
    font-weight: 700;
    font-size: 23px;
    line-height: 26px;
    color: var(--brand-green);
  }
  .person-role { font-size: 14.5px; line-height: 17px; margin-top: -2px; }
  .contact-list { list-style: none; margin-top: 6px; }
  .contact-list li {
    display: flex;
    align-items: center;
    gap: 4px;
    font-size: 14.5px;
    line-height: 18px;
  }
  .contact-list svg { width: 12px; height: 12px; fill: var(--brand-green); flex: none; }
  .address { font-size: 14.5px; line-height: 18px; margin-top: 7px; }
  .card-back .brand-mark {
    top: 230px;
    color: var(--white);
    font-size: 26px;
  }
  .card-back .brand-mark .dot {
    width: 24px; height: 24px;
    background: var(--white);
  }
  .since {
    position: absolute;
    top: 272px;
    left: 0; right: 0;
    text-align: center;
    color: var(--white);
    font-weight: 600;
    font-size: 13px;
    letter-spacing: 2px;
    text-transform: uppercase;
  }
  .back-url {
    position: absolute;
    top: 440px;
    left: 0; right: 0;
    text-align: center;
    color: var(--white);
    font-weight: 600;
    font-size: 13px;
  }
</style>
</head>
<body>
  <section class="card card-front">
    <div class="brand-mark"><span class="dot"></span>T.K. Fenwick</div>
    <div class="company">
      <div class="company-name">T.K. Fenwick</div>
      <div class="company-sub">Manufacturing Company, Inc.</div>
    </div>
    <div class="contact">
      <div class="person-name">Dale Fenwick</div>
      <div class="person-role">Vice President</div>
      <ul class="contact-list">
        <li><svg viewBox="0 0 12 12"><path d="M1 5c0-2 2-3 5-3s5 1 5 3v1H8.5V4.5h-5V6H1zM3 6.5h6l1.5 4h-9z"/></svg>770-555-4821</li>
        <li><svg viewBox="0 0 12 12"><path d="M3.5 0h5a1 1 0 0 1 1 1v10a1 1 0 0 1-1 1h-5a1 1 0 0 1-1-1V1a1 1 0 0 1 1-1zm.5 1.5v8h4v-8zM6 10a.6.6 0 1 0 0 1.2A.6.6 0 0 0 6 10z"/></svg>770-555-3067</li>
        <li><svg viewBox="0 0 12 12"><path d="M1 2.5h10v7H1zM1.8 3.2 6 6.5l4.2-3.3z" fill-rule="evenodd"/></svg>dale@tkfenwick.example</li>
        <li><svg viewBox="0 0 12 12"><circle cx="6" cy="6" r="5.5"/><path d="M3 4h3v2H4zM7 7h2v2H7z" fill="#f3f3f3"/></svg>www.tkfenwick.example</li>
      </ul>
      <div class="address">4700 West Harbor Boulevard<br>Suite #150<br>Roswell, GA 30076</div>
    </div>
  </section>

  <section class="card card-back">
    <div class="brand-mark"><span class="dot"></span>T.K. Fenwick</div>
    <div class="since">Since 1918</div>
    <div class="back-url">www.tkfenwick.example</div>
  </section>
</body>
</html>
```